verdant terraces simple classy business card design

my name is colin barrow and I run a gardening business aimed at high class verdant terraces. the business name is verdant terraces and our logo was designed on pixel harbour .My clientel are anything from residential homes to businesses. I take pride in my work and know that I offer a service like no other in my area.
The business card will be used to represent my business and I want it to be not only rememberable, but simplistic and modern. Eye catching too. Of course I would like it relatable to gardening and appealing to the correct clientel - those being garden enthusiasts, prestigious homes and businesses that are after top of the line gardening services like no other on the market.
I am not a typical lawn mowing business so I don't want a typical card design that represents that. The gardens I work with are generally million dollar properties with owners who are very garden proud looking for upkeep and guidance from me along with sometimes whole new garden designs. I want the business cards to show to my clients that I take pride, as they do, in their garden. And I want them to know from my card that I am a professional, qualified horticulturist offering them a top of the line service for life. I want them to refer my business on. I want them to look at my business card and see class and professionalism in a modern unique bold way.
The card should be simple with the possibility of the logo on the front being embossed/debossed and my details on the back the card should have a organic garden feel it's very important to me that it is absolutely perfect
I am also very open to ideas and suggestions so look forward to seeing the designs. the business logo has been supplied with this project and I want the card to be double sided

Contact info is
Colin Barrow - Managing Director / Horticulturist
Phone : 0481 526 704
Email: colinbarrow@verdantterraces.example.au

Target Market(s)

high class gardens residential and commercial

Industry/Entity Type

Gardener

Contact Information for Business Card

Contact info is
Phone : 0481 526 704

PLEASE MAKE CARD DOUBLE SIDED

Requirements
Must have
• organic simple classy modern feel
• must flow with the current logo that has been supplied with this project
• Double sided
• Must explain in a simple way that I deal with high end gardens and I'm a qualified horticulturist
Nice to have
• embossed debossed logo
Should not have
• shouldn't be to busy or cheap looking

```html
<!DOCTYPE html>
<html lang="en">
<head>
<meta charset="utf-8">
<title>Verdant Terraces – Business Card</title>
<link rel="stylesheet" href="https://fonts.googleapis.com/css2?family=Tinos&family=Source+Sans+3:wght@400&display=swap">
<style>
  :root {
    --backdrop-top: #2a2a2a;
    --backdrop-bottom: #050505;
    --card-white: #ffffff;
    --card-green: #5b8b4f;
    --brand-green: #4a9637;
    --text-dark: #2e2e2e;
    --logo-white: #ffffff;
  }
  html, body {
    margin: 0;
    padding: 0;
    width: 1200px;
    height: 900px;
    overflow: hidden;
  }
  .stage {
    position: relative;
    width: 1200px;
    height: 900px;
    background: linear-gradient(180deg, var(--backdrop-top) 0%, #141414 60%, var(--backdrop-bottom) 100%);
  }
  .card {
    position: absolute;
    top: 306px;
    width: 439px;
    height: 271px;
    border-radius: 10px;
    overflow: hidden;
  }
  .card--front { left: 149px; background: var(--card-white); }
  .card--back  { left: 609px; background: var(--card-green); }

  .brand-name {
    position: absolute;
    font-family: "Tinos", "Times New Roman", serif;
    font-weight: 400;
    text-align: center;
    margin: 0;
    line-height: 1;
  }
  .brand-name span { display: block; }
  .brand-mark {
    position: absolute;
    border-radius: 50%;
  }

  .card--front .brand-mark {
    left: 88px; top: 92px; width: 48px; height: 48px;
    background: var(--brand-green);
  }
  .card--front .brand-name {
    left: 12px; top: 146px; width: 200px;
    color: var(--brand-green);
  }
  .card--front .brand-name .line-one { font-size: 25px; letter-spacing: 1px; }
  .card--front .brand-name .line-two { font-size: 14px; letter-spacing: 7px; margin-top: 5px; }

  .details {
    position: absolute;
    left: 222px;
    top: 50px;
    width: 210px;
    font-family: "Source Sans 3", "Myriad Pro", sans-serif;
    color: var(--text-dark);
  }
  .person-name {
    margin: 0;
    font-family: "Tinos", "Times New Roman", serif;
    font-weight: 400;
    font-size: 19px;
    line-height: 22px;
    color: var(--brand-green);
  }
  .person-role { margin: 3px 0 0 1px; font-size: 13px; line-height: 15px; }
  .address { margin: 16px 0 0; font-size: 13px; line-height: 16px; }
  .contact-list { list-style: none; margin: 16px 0 0; padding: 0; font-size: 13px; line-height: 16px; }
  .contact-list li { display: flex; align-items: center; gap: 6px; white-space: nowrap; }
  .contact-list .contact-email { font-size: 10.5px; }
  .contact-list .contact-web { font-size: 12px; }
  .contact-list svg { width: 10px; height: 10px; fill: var(--brand-green); flex: none; }

  .card--back .brand-mark {
    left: 187px; top: 70px; width: 64px; height: 64px;
    background: var(--logo-white);
  }
  .card--back .brand-name {
    left: 40px; top: 148px; width: 359px;
    color: var(--logo-white);
  }
  .card--back .brand-name .line-one { font-size: 38px; letter-spacing: 1px; }
  .card--back .brand-name .line-two { font-size: 20px; letter-spacing: 13px; margin-top: 8px; }
</style>
</head>
<body>
<main class="stage">
  <section class="card card--front" aria-label="Business card, details side">
    <div class="brand-mark" aria-hidden="true"></div>
    <p class="brand-name"><span class="line-one">VERDANT</span><span class="line-two">TERRACES</span></p>
    <div class="details">
      <h1 class="person-name">Colin Barrow</h1>
      <p class="person-role">Managing Director /<br>Horticulturist</p>
      <p class="address">1234, Address Goes Here<br>Country Name, 123456</p>
      <ul class="contact-list">
        <li><svg viewBox="0 0 10 10" aria-hidden="true"><path d="M1 3 Q5 0 9 3 L8 4.5 L6.5 3.8 L6.5 3 Q5 2.5 3.5 3 L3.5 3.8 L2 4.5 Z M2.5 5 H7.5 L8.5 9 H1.5 Z"/></svg>0481 526 704</li>
        <li class="contact-email"><svg viewBox="0 0 10 10" aria-hidden="true"><path d="M1 2.5 H9 V8 H1 Z M1.5 3 L5 5.8 L8.5 3" stroke="#fff" stroke-width="0.8"/></svg>colinbarrow@verdantterraces.example.au</li>
        <li class="contact-web"><svg viewBox="0 0 10 10" aria-hidden="true"><path d="M4 6 L6 4" stroke="var(--brand-green)" stroke-width="1.2" fill="none"/><path d="M2 5.5 L3.8 3.7 M6.2 6.3 L4.4 8.1 A1.5 1.5 0 0 1 2 6 Z M5.5 2 A1.5 1.5 0 0 1 8 4.5 L6.3 6.2" stroke="var(--brand-green)" stroke-width="1.1" fill="none"/></svg>www.verdantterraces.example.au</li>
      </ul>
    </div>
  </section>

  <section class="card card--back" role="img" aria-label="Brand side: green card with a faint repeated brand pattern and the Verdant Terraces name">
    <div class="brand-mark" aria-hidden="true"></div>
    <p class="brand-name"><span class="line-one">VERDANT</span><span class="line-two">TERRACES</span></p>
  </section>
</main>
</body>
</html>
```